Business Card Design

We are a manufacturing and distribution company with most of our customer base being supermarkets. We have established brand guidelines that are attached.

```html
<!DOCTYPE html>
<html lang="en">
<head>
<meta charset="utf-8">
<title>Veltaro Business Card</title>
<link href="https://fonts.googleapis.com/css2?family=Roboto:wght@400;700;900&display=swap" rel="stylesheet">
<style>
  :root {
    --bg: #e9e9e9;
    --brand-blue: #0767ac;
    --edge-red: #e3141b;
    --panel-white: #ffffff;
    --panel-grey: #e6e6e6;
    --ink: #1b1b1b;
    --card-black: #231f20;
    --deboss: #3b3839;
    --white: #ffffff;
  }
  * { margin: 0; padding: 0; box-sizing: border-box; }
  html, body { width: 1200px; height: 802px; overflow: hidden; background: var(--bg); }
  body { font-family: "Roboto", Arial, sans-serif; position: relative; }

  .card {
    position: absolute;
    width: 540px;
    height: 309px;
    border: 2px solid var(--edge-red);
    overflow: hidden;
    box-shadow: 0 6px 18px rgba(0,0,0,0.12);
  }
  .card-front { left: 40px; top: 246px; background: var(--brand-blue); }
  .card-back { left: 620px; top: 246px; background: var(--card-black); }

  .front-panel { position: absolute; inset: 0; }

  .panel-brand {
    position: absolute;
    left: 118px;
    top: 118px;
    display: flex;
    align-items: center;
    gap: 10px;
  }
  .brand-square {
    width: 20px; height: 20px;
    background: var(--brand-blue);
  }
  .panel-brand .brand-name {
    font-weight: 900;
    font-size: 32px;
    letter-spacing: 1px;
    color: var(--ink);
  }

  .contact-block {
    position: absolute;
    right: 22px;
    top: 22px;
    text-align: right;
    color: var(--white);
  }
  .contact-block .brand-name {
    font-weight: 900;
    font-size: 30px;
    letter-spacing: 1px;
    line-height: 1;
    margin-bottom: 20px;
  }
  .person-name { font-weight: 700; font-size: 14px; letter-spacing: 0.5px; }
  .person-role { font-size: 13px; margin-bottom: 20px; }
  .address { font-size: 13px; line-height: 1.3; margin-bottom: 20px; }
  .contact-line {
    font-size: 13px;
    line-height: 1.45;
    display: flex;
    justify-content: flex-end;
    align-items: center;
    gap: 6px;
  }
  .contact-line svg { width: 11px; height: 11px; }

  .back-brand {
    position: absolute;
    inset: 0;
    display: flex;
    flex-direction: column;
    align-items: center;
    justify-content: center;
    gap: 16px;
  }
  .back-square {
    width: 48px; height: 48px;
    background: var(--deboss);
  }
  .back-brand .brand-name {
    font-weight: 900;
    font-size: 48px;
    letter-spacing: 3px;
    color: var(--deboss);
  }
</style>
</head>
<body>
  <section class="card card-front">
    <svg class="front-panel" viewBox="0 0 536 305" preserveAspectRatio="none" aria-hidden="true">
      <defs>
        <linearGradient id="panelFill" x1="0" y1="0" x2="1" y2="0">
          <stop offset="0" stop-color="var(--panel-white)"/>
          <stop offset="1" stop-color="var(--panel-grey)"/>
        </linearGradient>
      </defs>
      <path d="M0 0 H110 L362 132 Q378 140 368 152 L200 305 H0 Z"
            fill="url(#panelFill)" stroke="var(--edge-red)" stroke-width="2.5"/>
    </svg>

    <div class="panel-brand">
      <span class="brand-square"></span>
      <span class="brand-name">VELTARO</span>
    </div>

    <div class="contact-block">
      <div class="brand-name">VELTARO</div>
      <div class="person-name">DANIEL MOORE</div>
      <div class="person-role">Manager</div>
      <div class="address">Your address, city<br>state, ZIP 0000</div>
      <div class="contact-line">555-018-4732
        <svg viewBox="0 0 12 12"><path d="M2.5 1 L4.5 1 L5.2 3.5 L4 4.5 Q5 7 7.5 8 L8.5 6.8 L11 7.5 L11 9.5 Q10.5 11 9 11 Q2 10 1 3 Q1 1.5 2.5 1 Z" fill="var(--white)"/></svg>
      </div>
      <div class="contact-line">youremail@mailbox.com
        <svg viewBox="0 0 12 12"><rect x="1" y="2.5" width="10" height="7" fill="none" stroke="var(--white)" stroke-width="1.2"/><path d="M1 2.5 L6 6.5 L11 2.5" fill="none" stroke="var(--white)" stroke-width="1.2"/></svg>
      </div>
      <div class="contact-line">www.yourdomain.net
        <svg viewBox="0 0 12 12"><circle cx="6" cy="6" r="5" fill="none" stroke="var(--white)" stroke-width="1.2"/><path d="M1 6 H11 M6 1 Q3 6 6 11 M6 1 Q9 6 6 11" fill="none" stroke="var(--white)" stroke-width="1"/></svg>
      </div>
    </div>
  </section>

  <section class="card card-back">
    <div class="back-brand">
      <span class="back-square"></span>
      <span class="brand-name">VELTARO</span>
    </div>
  </section>
</body>
</html>
```